Lanternfield Drinks business cards

We need a business card design for our new logo. The company is modern, progressive, professional, yet approachable. The key products are ready to drink bottles and cans of coffee based beverages.
These cards will be a critical part of the first impression made by our sales organization, business development team, and all external facing personnel.
Card can be a vertical or horizontal orientation.

Target Market(s)

Customers, suppliers, business partners

Industry/Entity Type

Business

Contact Information for Business Card

Business cards should feature Company Name and Logo.

Font styles to use
Serif

Colors

Designer to choose colors to be used in the design.

Requirements
Must have
• Strong readability of Name, phone #, mobile number and email address.
• Job title, website url, Street Address, and other details can be secondary level readability.
Nice to have
• High impact, simplistic quality design.
• Ok to utilize the 'H in the box' separate from the company name

```html
<!DOCTYPE html>
<html lang="en">
<head>
<meta charset="utf-8">
<title>Lanternfield Drinks business cards</title>
<link rel="stylesheet" href="https://fonts.googleapis.com/css2?family=Crimson+Pro:wght@400;600;700&display=swap">
<style>
  :root {
    --backdrop: #3b3b3d;
    --card: #1e1e1f;
    --orange: #e0552f;
    --amber: #f0962a;
    --white: #f4f1ec;
  }
  * { margin: 0; padding: 0; box-sizing: border-box; }
  html, body { width: 799px; height: 1200px; overflow: hidden; }
  body {
    background: var(--backdrop);
    font-family: "Crimson Pro", Georgia, serif;
    position: relative;
  }
  .card {
    position: absolute;
    left: 90px;
    width: 620px;
    height: 354px;
    background: var(--card);
    overflow: hidden;
    box-shadow: 0 18px 40px rgba(0,0,0,.45);
  }
  .card--front { top: 120px; }
  .card--back { top: 720px; }

  .brand { display: flex; align-items: center; gap: 12px; }
  .brand__mark { width: 34px; height: 34px; border: 3px solid var(--orange); flex: none; }
  .brand__name {
    color: var(--orange);
    font-weight: 700;
    font-size: 30px;
    letter-spacing: 1px;
    text-transform: uppercase;
    line-height: 1;
  }
  .brand__rule { height: 2px; background: var(--amber); }

  .card--front .brand-block {
    position: absolute; left: 0; right: 0; top: 108px;
    display: flex; flex-direction: column; align-items: center; gap: 12px;
  }
  .card--front .brand__rule { width: 420px; }
  .website {
    position: absolute; left: 0; right: 0; top: 260px;
    display: flex; align-items: center; justify-content: center; gap: 18px;
    color: var(--white); font-size: 18px; letter-spacing: .5px;
  }
  .website__accent { color: var(--orange); }
  .website__dash { width: 48px; height: 3px; background: var(--orange); }

  .swoosh { position: absolute; inset: 0; }

  .card--back .brand-block {
    position: absolute; left: 40px; top: 120px;
    display: flex; flex-direction: column; gap: 10px;
  }
  .card--back .brand__name { font-size: 24px; }
  .card--back .brand__mark { width: 28px; height: 28px; }
  .card--back .brand__rule { width: 330px; }
  .address {
    position: absolute; left: 40px; top: 200px;
    color: var(--white); font-size: 16px; line-height: 1.3;
  }
  .person {
    position: absolute; right: 30px; top: 92px; text-align: right; color: var(--white);
  }
  .person__name { font-size: 26px; font-weight: 700; line-height: 1.1; }
  .person__title { font-size: 15px; }
  .contacts {
    position: absolute; right: 26px; bottom: 24px;
    list-style: none; color: var(--white); font-size: 16px; line-height: 1.45;
  }
  .contacts li { display: flex; align-items: center; justify-content: flex-end; gap: 10px; }
  .contacts svg { width: 14px; height: 14px; fill: var(--orange); }
</style>
</head>
<body>
  <section class="card card--front">
    <div class="brand-block">
      <div class="brand">
        <span class="brand__mark"></span>
        <span class="brand__name">Lanternfield Drinks Co.</span>
      </div>
      <div class="brand__rule"></div>
    </div>
    <div class="website">
      <span class="website__dash"></span>
      <span>www.<span class="website__accent">lanternfielddrinks</span>.com</span>
      <span class="website__dash"></span>
    </div>
  </section>

  <section class="card card--back">
    <svg class="swoosh" viewBox="0 0 620 354" aria-hidden="true">
      <path d="M0,0 H620 V268 C560,262 505,235 460,170 C405,90 300,22 0,12 Z" fill="var(--orange)"/>
      <path d="M0,30 C300,40 400,100 455,185 C500,255 560,282 620,290" fill="none" stroke="var(--card)" stroke-width="10"/>
      <path d="M0,34 C300,46 398,108 452,192 C498,262 560,290 620,298" fill="none" stroke="var(--amber)" stroke-width="6"/>
    </svg>

    <div class="person">
      <div class="person__name">Evan Marlow Reyes</div>
      <div class="person__title">Managing Director</div>
    </div>

    <div class="brand-block">
      <div class="brand">
        <span class="brand__mark"></span>
        <span class="brand__name">Lanternfield Drinks Co.</span>
      </div>
      <div class="brand__rule"></div>
    </div>

    <p class="address">18 Orchard Lane,<br>Fairview, US 40213</p>

    <ul class="contacts">
      <li>555.014.2231
        <svg viewBox="0 0 16 16"><path d="M3 1h3l1 4-2 1c1 2 3 4 5 5l1-2 4 1v3c0 1-1 2-2 2C7 15 1 9 1 3c0-1 1-2 2-2z"/></svg></li>
      <li>555.019.4478
        <svg viewBox="0 0 16 16"><path d="M4 0h8a1 1 0 0 1 1 1v14a1 1 0 0 1-1 1H4a1 1 0 0 1-1-1V1a1 1 0 0 1 1-1zm1 2v10h6V2z"/></svg></li>
      <li>evan@lanternfielddrinks.com
        <svg viewBox="0 0 16 16"><path d="M1 3h14v10H1zm1 1v1l6 4 6-4V4z"/></svg></li>
      <li>www.lanternfielddrinks.com
        <svg viewBox="0 0 16 16"><circle cx="8" cy="8" r="7"/><path d="M1 8h14M8 1v14" stroke="#1e1e1f" stroke-width="1.2"/></svg></li>
    </ul>
  </section>
</body>
</html>
```